Website for a financial survey consultancy

WHO WE ARE
We're a niche HR consultancy specialising in salary comparison surveys for the financial asset management industry. We position ourselves as a small, highly responsive organisation with a strong personal relationship with each of our 50+ blue-chip clients.

WHAT WE DO
Our business is 80% surveys (= products), 20% consultancy (= services). The surveys are a set of online products which clients interact with to find the information they are interested in.

WHAT WE WANT
We are completely revising our existing marketing website and need a new up-to-date look and feel for the site. We want you to design 2 web pages
- Home page
- Internal content page

More details below in Must Have Priorities.

REFERENCE SITES
- www.veltramoor.com - nice background image
- www.plimweather.com - ignoring the animations
- www.gasketvale.com
- www.quorbin.com - clean, fresh, styly but prob not corporate enough
- www.dulveropinex.com - spacious, beautiful, slightly dated tho
- www.tambly.co.uk - ignore the colours. Like the simplicity, larger font size (although want to stick with sans-serif fonts for main content)

DELIVERABLES
The final designs should be delivered as one or more PSD files with clearly named layers. All design elements and treatments should be separated out, for example use adjustment layers rather than applied (and subsequently irreversible) adjustments, strokes, shading, etc.

WHAT NEXT
I'll be monitoring the contest every day and can respond to questions fast. You can IM me on Chatterlyne or QBX.

Reason: Hi folks,

I am extending the deadline to this project as I am travelling this week and therefore will not be able to make a final decision until next Monday. I will try and provide further feedback over the course of this week but I am only going to be online occasionally so be prepared to wait a few days for a reply from me.

Thanks for all the designs so far.

Tobias

Target Market(s)

In order of importance, most important first

1. Potential customers - UK & US financial industry HR professionals, short on time. Heard about us already, want to find out more about what we do, confirm relevance for their needs. Core goal - establish credibility: are we properly resourced, will we be around for years to come, are we *real*.

2. Existing customers - UK & US financial industry professionals, short on time, under pressure, want results quickly, minimum faff, expect high quality, slickly presented information. Primary action: login and use surveys.

3. Industry professionals/researchers - probably arriving through blog content, looking to browse and hoover information. Valuable for their ability to spread awareness of who we are amongst their peers.

Industry/Entity Type

Financial

Requirements
Must have
• GENERAL
Style cues - Corporate, professional, financial, stylish, slick, clean, spacious, light
Size - standard 960px grid

NAVIGATION
- [ Home | About us | Surveys | Consulting | Blog ]
- Sub-nav (roll-over dropdown) on About Us, Surveys & Consulting

ALL PAGES
- Site navigation
- Client login (on screen permanently or link to ajaxy in-page pop-up)
- Footer section
- Existing logo (attached)* - this is obviously an important reference point in the design, esp colour

HOME PAGE
- Communicate (link thru to?) survey/consulting split
- Large photo(s)/backdrop (2-3 interchangeable options ideally). Please consider what rights agreement will be necessary for any photos you include in your design.
- Possibly bigger more prominent version of logo
- Strap line/sentence - "Focussed data is the key to success"
- 3 recent blog posts (should look good with and without blog post images)
- Free downloadable PDF research report + supporting blurb

INTERNAL PAGE
- Page title
- Content - typical page will be less than one screenfull
- Level 1 sub-heading
- Level 2 sub-heading
- Bulleted list
- Content supporting image (any image will do - interested in placement, borders (if any), spacing, caption, etc)
- 'Do something' button

* Note: there is some internal debate about this logo at the moment. Some (me) are keen for it to change, some (not me!) are not. If you have an web page design idea/concept that requires an evolution of the logo, go ahead and evolve it. We can explore this further in the design process as necessary, but don't sweat it.
Nice to have
• Values to communicate
- Knowledgeable
- Professional
- Secure
- Personal
- Experienced
- Financial industry specific
- Accurate
- Reliable
Should not have
• - Search box
- Social media links, other than RSS feed button (discrete)

```html
<!DOCTYPE html>
<html lang="en">
<head>
<meta charset="utf-8">
<title>Corvanel – HR consultancy</title>
<link href="https://fonts.googleapis.com/css2?family=Arimo:wght@400;700&family=Roboto+Condensed:wght@400&display=swap" rel="stylesheet">
<style>
:root{
  --page-bg:#d6ecfb;
  --nav-top:#4a5459;
  --nav-bottom:#343d42;
  --brand-red:#6b0a0a;
  --sky-top:#3f86e6;
  --sky-bottom:#a9cdf2;
  --panel-dark:rgba(28,42,52,.93);
  --accent-blue:#5f95e0;
  --sidebar-bg:rgba(245,249,254,.93);
  --login-bg:#6b98cc;
  --login-title:#f2e640;
  --footer-bg:#03080d;
  --text-light:#ffffff;
  --text-dark:#333333;
  --arrow-orange:#e05a00;
  --arrow-blue:#7fb8ff;
  --thumb-border:#8f9499;
}
*{box-sizing:border-box;margin:0;padding:0}
html,body{width:1200px;height:900px;overflow:hidden}
body{background:var(--page-bg);font-family:"Arimo",Arial,sans-serif;position:relative}
.site{position:absolute;left:121px;top:24px;width:964px;height:851px}

.main-nav{position:absolute;left:0;top:0;width:964px;height:48px;background:linear-gradient(var(--nav-top),var(--nav-bottom))}
.main-nav a,.main-nav .sep{position:absolute;top:17px;color:var(--text-light);text-decoration:none;font-size:12px;font-weight:400;letter-spacing:-.3px;line-height:14px}

.hero{position:absolute;left:0;top:48px;width:964px;height:592px;overflow:hidden}
.hero-photo{position:absolute;inset:0;background:linear-gradient(160deg,#2f6fd0 0%,var(--sky-top) 35%,var(--sky-bottom) 85%,#c9d3dc 100%)}

.brand{position:absolute;display:flex;align-items:center;gap:8px;color:var(--text-light);font-weight:700}
.brand-dot{width:12px;height:12px;background:var(--brand-red)}
.hero-brand{left:24px;top:22px;font-size:22px}

.intro{position:absolute;left:25px;top:210px;width:443px;height:302px;background:var(--panel-dark);padding:26px 20px 0 16px}
.intro h1{color:var(--text-light);font-size:54px;font-weight:700;line-height:1;letter-spacing:-.3px}
.intro .tagline{color:var(--accent-blue);font-size:20px;line-height:28px;margin-top:10px;padding-left:1px;letter-spacing:-.3px}
.intro .body{color:var(--text-light);font-size:13px;line-height:17px;text-align:justify;margin-top:16px;padding-left:4px;padding-right:6px;hyphens:auto}

.sidebar{position:absolute;left:670px;top:0;width:261px;height:592px;background:var(--sidebar-bg)}
.login{position:absolute;left:8px;top:64px;width:247px;height:179px;background:var(--login-bg);padding:15px 8px 0}
.login h2{color:var(--login-title);font-size:13px;font-weight:700}
.login label{display:block;color:var(--text-light);font-size:12px;margin-top:9px}
.login .field{display:block;width:225px;height:22px;background:#fff;margin-top:3px}
.login-actions{display:flex;align-items:center;margin-top:11px}
.login-btn{width:72px;height:26px;border-radius:6px;background:linear-gradient(#fff,#e2e8ef);border:1px solid #c4cfdc;color:#1f3e72;font-size:12px;display:flex;align-items:center;justify-content:center}
.forgot{color:#e8f1ff;font-size:11px;font-weight:700;margin-left:5px}

.blogs{position:absolute;left:10px;top:272px}
.blogs h2{font-family:"Roboto Condensed","Arial Narrow",sans-serif;font-weight:400;font-size:22px;color:#111;letter-spacing:-.3px}
.blog-item{position:absolute;left:-1px;width:240px}
.blog-thumb{position:absolute;left:0;top:0;width:53px;height:53px;border:3px solid var(--thumb-border);background:linear-gradient(#9fb2c4,#6d7f8f)}
.blog-text{position:absolute;left:60px;top:-2px;width:162px;font-size:11px;font-weight:700;color:var(--text-dark);line-height:13.5px}
.read-more{position:absolute;left:61px;font-size:10px;color:#111;text-decoration:underline;white-space:nowrap}
.read-more b{color:var(--arrow-orange);display:inline-block;margin-left:3px;font-size:12px}

.footer{position:absolute;left:0;top:640px;width:964px;height:211px;background:var(--footer-bg)}
.footer-btn{position:absolute;top:24px;width:91px;height:34px;background:linear-gradient(#fdfdfd,#a8a8a8);border:1px solid #5a5a5a;display:flex;align-items:center;justify-content:center;font-size:13px;font-weight:700;color:#111}
.footer-text{position:absolute;color:var(--text-light);font-size:12px;line-height:16px;text-align:justify}
.footer-thumb{position:absolute;top:84px;width:70px;height:70px;border:3px solid var(--thumb-border)}
.learn{position:absolute;top:185px;color:var(--text-light);font-size:12px;text-decoration:none;white-space:nowrap}
.learn b{color:var(--arrow-blue);margin-left:3px}
.footer-brand{left:812px;top:30px;font-size:17px}
.copyright{position:absolute;left:784px;top:185px;color:#a7adb3;font-size:10px;white-space:nowrap}
</style>
</head>
<body>
<div class="site">
  <nav class="main-nav">
    <a href="#" style="left:37px">HOME</a><span class="sep" style="left:100px">|</span>
    <a href="#" style="left:138px">ABOUT US</a><span class="sep" style="left:221px">|</span>
    <a href="#" style="left:258px">SURVEYS</a><span class="sep" style="left:335px">|</span>
    <a href="#" style="left:372px">CONSULTING</a><span class="sep" style="left:470px">|</span>
    <a href="#" style="left:508px">BLOG</a>
  </nav>

  <section class="hero">
    <div class="hero-photo" role="img" aria-label="Photo of a long curved concrete bridge seen from below against a blue sky"></div>

    <div class="brand hero-brand"><span class="brand-dot"></span>Corvanel</div>

    <div class="intro">
      <h1>HR consultancy</h1>
      <p class="tagline">specialising in salary comparison surveys for the financial asset management industry</p>
      <p class="body">Lorem ipsum dolor sit amet, consectetur adipiscing elit. Cras ante dui, viverra non vehicula in, condimentum id ipsum. Fusce at arcu metus. Fusce eu justo nisl. Maecenas consequat condimentum ante, quis tincidunt neque viverra sed. Aenean tempus rhoncus dolor, at dapibus ipsum dapibus at. Nulla ac turpis a quam venenatis molestie sit amet ut enim. Sed elementum feugiat bibendum. Morbi sed adipiscing tellus.</p>
    </div>

    <aside class="sidebar">
      <form class="login">
        <h2>Client LOGIN</h2>
        <label>User Name<span class="field"></span></label>
        <label>Password<span class="field"></span></label>
        <div class="login-actions">
          <span class="login-btn">LOGIN ››</span>
          <span class="forgot">Forgot Password?</span>
        </div>
      </form>

      <div class="blogs">
        <h2>Latest Blogs</h2>
        <div class="blog-item" style="top:41px">
          <div class="blog-thumb" role="img" aria-label="Portrait photo of a blog author"></div>
          <p class="blog-text">Lorem ipsum dolor sit amet, consectetur adipiscing elit. Cras ante du</p>
          <a class="read-more" href="#" style="top:44px">Read More<b>»</b></a>
        </div>
        <div class="blog-item" style="top:124px">
          <div class="blog-thumb" role="img" aria-label="Portrait photo of a blog author"></div>
          <p class="blog-text">Lorem ipsum dolor sit amet, consectetur adipiscing elit. Cras ante du</p>
          <a class="read-more" href="#" style="top:44px">Read More<b>»</b></a>
        </div>
        <div class="blog-item" style="top:205px">
          <div class="blog-thumb" role="img" aria-label="Portrait photo of a blog author"></div>
          <p class="blog-text">Lorem ipsum dolor sit amet, consectetur adipiscing elit. Cras ante du</p>
          <a class="read-more" href="#" style="top:41px">Read More<b>»</b></a>
        </div>
      </div>
    </aside>
  </section>

  <footer class="footer">
    <div class="footer-btn" style="left:22px">About us</div>
    <p class="footer-text" style="left:22px;top:83px;width:172px">Lorem ipsum dolor sit amet, consectetur adipiscing elit. Cras ante dui, viverra non vehicula in, condimentum id ipsum. Fusce at arcu metus.</p>

    <div class="footer-btn" style="left:262px">Surveys</div>
    <div class="footer-thumb" style="left:264px;background:linear-gradient(#cfd8e0,#8b98a6)" role="img" aria-label="Photo of a smiling man sitting cross-legged with a laptop"></div>
    <p class="footer-text" style="left:344px;top:82px;width:140px;text-align:left">Lorem ipsum dolor sit amet, consectetur adipiscing elit. Cras ante dui, viverra non vehicula in, condimentum</p>
    <a class="learn" href="#" style="left:345px">Learn More<b>››</b></a>

    <div class="footer-btn" style="left:522px">Consulting</div>
    <div class="footer-thumb" style="left:522px;background:linear-gradient(#d9cfc6,#9a8a7e)" role="img" aria-label="Photo of a smiling woman reaching out for a handshake"></div>
    <p class="footer-text" style="left:602px;top:82px;width:140px">Fusce at arcu metus. eu justo nisl. Maecenas consequat condimentum ante, quis tincidunt neque viverra sed.</p>
    <a class="learn" href="#" style="left:603px">Learn More<b>››</b></a>

    <div class="brand footer-brand"><span class="brand-dot"></span>Corvanel</div>
    <p class="copyright">© 2011 Corvanel. All rights reserved</p>
  </footer>
</div>
</body>
</html>
```